Veldmark Supplies Business Card

Professional business card that stand out to our potential customers. Front and back with clean modern design

Industry/Entity Type

Oil and gas

Contact Information for Business Card

Name, address, website , office phone and cell number

Requirements
Must have
• Editable files for each employee

```html
<!DOCTYPE html>
<html lang="en">
<head>
<meta charset="UTF-8">
<title>Veldmark Supplies Business Card</title>
<link href="https://fonts.googleapis.com/css2?family=Poppins:wght@400;700&display=swap" rel="stylesheet">
<style>
  :root {
    --page-bg: #dfe4e6;
    --card-dark: #1e1e1e;
    --brand-red: #ec2527;
    --brand-blue: #17b1d3;
    --mid-tone: #a08a80;
    --white: #ffffff;
  }
  * { margin: 0; padding: 0; box-sizing: border-box; }
  html, body {
    width: 1200px; height: 960px; overflow: hidden;
    background: var(--page-bg);
    font-family: "Poppins", sans-serif;
  }
  .card {
    position: absolute; left: 249px; width: 702px; height: 400px; overflow: hidden;
  }
  /* Front */
  .card-front {
    top: 60px;
    background: linear-gradient(to bottom, var(--brand-blue) 0%, var(--mid-tone) 45%, var(--brand-red) 100%);
  }
  .front-brand {
    position: absolute; left: 0; right: 0; top: 120px;
    display: flex; flex-direction: column; align-items: center; gap: 28px;
  }
  .front-brand .brand-square {
    width: 92px; height: 92px; background: var(--white);
  }
  .front-brand .brand-name {
    color: var(--white); font-weight: 700; font-size: 34px; letter-spacing: 2px; line-height: 1;
  }
  /* Back */
  .card-back { top: 500px; background: var(--card-dark); }
  .back-brand {
    position: absolute; left: 25px; top: 120px;
    display: flex; align-items: center; gap: 12px;
  }
  .back-brand .brand-square { width: 26px; height: 26px; background: var(--brand-red); }
  .back-brand .brand-name {
    color: var(--brand-red); font-weight: 700; font-size: 20px; letter-spacing: 1px;
  }
  .person {
    position: absolute; right: 27px; top: 24px; text-align: right;
  }
  .person-name { color: var(--brand-red); font-size: 35px; line-height: 1.1; }
  .person-name .first { font-weight: 700; }
  .person-name .last { font-weight: 400; }
  .person-role { color: var(--brand-blue); font-size: 19px; line-height: 1.4; }
  .accent-bar {
    position: absolute; right: 0; top: 31px; width: 19px; height: 54px; background: var(--brand-blue);
  }
  .address {
    position: absolute; left: 23px; top: 208px;
    color: var(--brand-blue); font-size: 18px; line-height: 24px; letter-spacing: 0.3px;
  }
  .contact-band {
    position: absolute; left: 0; right: 0; bottom: 0; height: 128px;
    background: linear-gradient(to right, var(--brand-red) 0%, var(--mid-tone) 45%, var(--brand-blue) 95%);
  }
  .contact-list {
    position: absolute; left: 26px; top: 13px; list-style: none;
  }
  .contact-list li {
    display: flex; align-items: center; gap: 12px;
    color: var(--white); font-size: 18px; line-height: 24px;
  }
  .contact-list svg { width: 16px; height: 16px; flex: none; }
</style>
</head>
<body>

<section class="card card-front">
  <div class="front-brand">
    <div class="brand-square"></div>
    <div class="brand-name">VELDMARK SUPPLIES</div>
  </div>
</section>

<section class="card card-back">
  <div class="back-brand">
    <div class="brand-square"></div>
    <div class="brand-name">VELDMARK SUPPLIES</div>
  </div>

  <div class="person">
    <div class="person-name"><span class="first">Mirela</span> <span class="last">Hostova</span></div>
    <div class="person-role">Co-Founder &amp; CEO</div>
  </div>
  <div class="accent-bar"></div>

  <address class="address" style="font-style:normal">
    408 Larkspur Avenue,<br>Midland, TX 79701
  </address>

  <div class="contact-band">
    <ul class="contact-list">
      <li>
        <svg viewBox="0 0 24 24" fill="none" stroke="#fff" stroke-width="2.4" stroke-linecap="round" stroke-linejoin="round"><path d="M5 3h4l2 5-2.5 1.5a11 11 0 0 0 6 6L16 13l5 2v4a2 2 0 0 1-2 2A16 16 0 0 1 3 5a2 2 0 0 1 2-2z"/></svg>
        <span>(432) 555-0147</span>
      </li>
      <li>
        <svg viewBox="0 0 24 24" fill="none" stroke="#fff" stroke-width="2.4"><rect x="6" y="2" width="12" height="20" rx="2"/></svg>
        <span>(432) 555-0193</span>
      </li>
      <li>
        <svg viewBox="0 0 24 24" fill="none" stroke="#fff" stroke-width="2.2"><circle cx="12" cy="12" r="10"/><path d="M2 12h20M12 2c3 3 3 17 0 20M12 2c-3 3-3 17 0 20"/></svg>
        <span>www.website.com</span>
      </li>
      <li>
        <svg viewBox="0 0 24 24" fill="none" stroke="#fff" stroke-width="2.2" stroke-linejoin="round"><rect x="2" y="5" width="20" height="15" rx="1"/><path d="M2 6l10 8 10-8"/></svg>
        <span>info@website.com</span>
      </li>
    </ul>
  </div>
</section>

</body>
</html>
```